Garlic Farm for Farm Sales/Restaurant sales

Need a professional, but appealing to agriculture world. We are selling 27 kinds of Organic Garlic from a farm in Simla,CO. I have uploaded logo and business information-we are going to need a template, because I will need to use it for four separate people.
-We are trying to appeal to Farm to table restaurants
-As well as growers/farmers

Target Market(s)

Agriculture Sales/Restaurants-Organic

Industry/Entity Type

Agriculture

Contact Information for Business Card

Want it to look more unique then your average kelto stock card- I want it to look amazing

Font styles to use
Sans Serif

Colors
0455a3
ec1f27
fbed22
ffffff

Requirements
Must have
• Just be creative
Nice to have
• Colorful
Should not have
• plain

```html
<!DOCTYPE html>
<html lang="en">
<head>
<meta charset="utf-8">
<title>Plainsridge Garlic — Business Card</title>
<link rel="stylesheet" href="https://fonts.googleapis.com/css2?family=Source+Sans+3:ital,wght@0,400;0,600;0,700;1,600&display=swap">
<style>
  :root {
    --backdrop: #e9e6e2;
    --card-yellow: #ffd900;
    --card-red: #c20a2e;
    --brand-blue: #1d3a78;
    --text-dark: #1b1b1b;
    --icon-red: #c20a2e;
    --bulb-white: #ffffff;
  }
  * { margin: 0; padding: 0; box-sizing: border-box; }
  html, body {
    width: 1200px;
    height: 900px;
    overflow: hidden;
    background: var(--backdrop);
    font-family: "Source Sans 3", "Helvetica Neue", Arial, sans-serif;
  }
  .canvas {
    position: relative;
    width: 1200px;
    height: 900px;
  }
  .business-card {
    position: absolute;
    left: 120px;
    top: 152px;
    width: 960px;
    height: 596px;
    background: var(--card-yellow);
    overflow: hidden;
    box-shadow: 0 10px 30px rgba(0, 0, 0, 0.18);
  }
  .side-band {
    position: absolute;
    top: 0;
    right: 0;
    width: 182px;
    height: 100%;
    background: var(--card-red);
  }
  .bulb-art {
    position: absolute;
    left: 462px;
    top: 20px;
    width: 498px;
    height: 576px;
    background:
      radial-gradient(ellipse 46% 52% at 52% 66%,
        rgba(255, 255, 255, 0.95) 0%,
        rgba(255, 255, 255, 0.8) 45%,
        rgba(255, 255, 255, 0.35) 75%,
        rgba(255, 255, 255, 0) 100%);
  }
  .brand {
    position: absolute;
    left: 54px;
    top: 58px;
    display: flex;
    align-items: center;
    gap: 18px;
  }
  .brand-dot {
    width: 96px;
    height: 96px;
    border-radius: 50%;
    background: var(--card-red);
  }
  .brand-name {
    font-weight: 700;
    font-size: 36px;
    color: var(--brand-blue);
    letter-spacing: 0.3px;
  }
  .person {
    position: absolute;
    left: 71px;
    top: 238px;
  }
  .person-name {
    font-style: italic;
    font-weight: 600;
    font-size: 38px;
    color: var(--card-red);
    line-height: 1.1;
  }
  .person-role {
    font-size: 29px;
    color: var(--text-dark);
    margin-top: 2px;
  }
  .contact-list {
    position: absolute;
    left: 71px;
    top: 338px;
    list-style: none;
  }
  .contact-list li {
    display: flex;
    align-items: center;
    gap: 12px;
    height: 35px;
    font-size: 25px;
    color: var(--text-dark);
  }
  .contact-list svg {
    width: 20px;
    height: 20px;
    fill: var(--icon-red);
    flex: none;
  }
  .address {
    position: absolute;
    left: 71px;
    top: 503px;
    font-size: 27px;
    color: var(--text-dark);
  }
</style>
</head>
<body>
<main class="canvas">
  <section class="business-card">
    <div class="side-band"></div>
    <div class="bulb-art" role="img" aria-label="Large white garlic bulb illustration with red and yellow clove lines"></div>

    <header class="brand">
      <span class="brand-dot"></span>
      <span class="brand-name">Plainsridge Garlic</span>
    </header>

    <div class="person">
      <p class="person-name">Dana Whitfield</p>
      <p class="person-role">Owner</p>
    </div>

    <ul class="contact-list">
      <li>
        <svg viewBox="0 0 20 20" aria-hidden="true"><path d="M2 7c0-3 3-5 8-5s8 2 8 5v1h-4V6.5c-1-.6-2.4-.9-4-.9s-3 .3-4 .9V8H2zM5 9h10l2 8H3z"/></svg>
        <span>719-555-0148</span>
      </li>
      <li>
        <svg viewBox="0 0 20 20" aria-hidden="true"><path d="M5 1h8l2 2v4h2v12H3V7h2zm2 2v4h6V3.8L12.2 3zM6 10v2h2v-2zm4 0v2h2v-2zm-4 4v2h2v-2zm4 0v2h2v-2z"/></svg>
        <span>(719)-555-0162</span>
      </li>
      <li>
        <svg viewBox="0 0 20 20" aria-hidden="true"><path d="M1 4h18v12H1zm2 2v.4l7 4.6 7-4.6V6zm0 2.8V14h14V8.8l-7 4.6z"/></svg>
        <span>hello@plainsridgegarlic.com</span>
      </li>
      <li>
        <svg viewBox="0 0 20 20" aria-hidden="true"><circle cx="10" cy="10" r="9"/><path d="M4 8c2-1 3 1 5 0s1-3 3-3M8 17c0-2 2-3 3-2s3 0 3-2" stroke="#ffd900" stroke-width="1.6" fill="none"/></svg>
        <span>www.plainsridgegarlic.com</span>
      </li>
    </ul>

    <p class="address">PO Box 2071, Simla, CO 80835</p>
  </section>
</main>
</body>
</html>
```